Business Card Design

New business card design

Target Market(s)

Residential & Commercial Property Managers

Industry/Entity Type

Plumbing Services

Contact Information for Business Card

Name - Rowan Keddle, title - Director, Phone Number - 0431 286 517, email - rowan@tbk-plumbing.com.au, Company ABN - 73 215 904 386,

Font styles to use
Sans Serif

Colors
0054AA
0677BA
7BADD7
CADEEF
E8F1F8

```html
<!DOCTYPE html>
<html lang="en">
<head>
<meta charset="utf-8">
<title>TBK Plumbing Services – Business Card</title>
<link href="https://fonts.googleapis.com/css2?family=Montserrat:wght@300;400;700&display=swap" rel="stylesheet">
<style>
  :root {
    --bg: #cfd4d4;
    --card: #efefed;
    --ink: #1b1b1d;
    --muted: #3a3a3c;
    --brand-blue: #2aa8e0;
    --deep-blue: #0677ba;
    --white: #ffffff;
  }
  * { margin: 0; padding: 0; box-sizing: border-box; }
  html, body {
    width: 1200px; height: 881px; overflow: hidden;
    background: var(--bg);
    font-family: "Montserrat", Arial, sans-serif;
  }
  .stage {
    position: relative; width: 1200px; height: 881px;
    display: flex; align-items: center; justify-content: center; gap: 50px;
  }
  .card {
    position: relative; width: 520px; height: 318px;
    background: var(--card);
    box-shadow: 0 10px 28px rgba(0,0,0,0.18);
    overflow: hidden;
  }
  .card--back { border-bottom: 4px solid var(--deep-blue); }

  /* Front */
  .wordmark {
    position: absolute; left: 34px; top: 62px; width: 210px;
    color: var(--ink); font-weight: 300; text-align: center;
  }
  .wordmark__name { font-size: 74px; line-height: 1; letter-spacing: 2px; }
  .wordmark__tag { font-size: 10px; letter-spacing: 6px; margin-top: 6px; }
  .divider {
    position: absolute; left: 270px; top: 58px; width: 1.5px; height: 150px;
    background: var(--brand-blue);
  }
  .contact { position: absolute; left: 290px; top: 66px; }
  .contact__name { color: var(--brand-blue); font-weight: 700; font-size: 21px; }
  .contact__title { color: var(--muted); font-size: 13px; margin-top: 2px; }
  .contact__list { list-style: none; margin-top: 22px; }
  .contact__item {
    display: flex; align-items: center; gap: 7px;
    color: var(--muted); font-size: 12.5px; margin-bottom: 8px;
  }
  .contact__icon { width: 12px; height: 12px; flex: none; }
  .abn-band {
    position: absolute; left: 0; right: 0; bottom: 14px; height: 34px;
    background: var(--brand-blue); color: var(--white);
    font-size: 12.5px; display: flex; align-items: center; padding-left: 118px;
  }

  /* Back */
  .back-mark {
    position: absolute; inset: 0;
    display: flex; flex-direction: column; align-items: center; justify-content: center;
    color: var(--ink); font-weight: 300;
  }
  .back-mark__row { display: flex; align-items: center; gap: 14px; }
  .back-mark__name { font-size: 120px; line-height: 1; letter-spacing: 4px; }
  .back-mark__dot { width: 22px; height: 22px; border-radius: 50%; background: var(--brand-blue); }
  .back-mark__tag { font-size: 14px; letter-spacing: 12px; margin-top: 10px; }
</style>
</head>
<body>
<main class="stage">
  <section class="card card--front" aria-label="Card front">
    <div class="wordmark">
      <div class="wordmark__name">tbk</div>
      <div class="wordmark__tag">plumbing services</div>
    </div>
    <div class="divider"></div>
    <div class="contact">
      <p class="contact__name">Rowan Keddle</p>
      <p class="contact__title">Director</p>
      <ul class="contact__list">
        <li class="contact__item">
          <svg class="contact__icon" viewBox="0 0 24 24" aria-hidden="true"><path fill="#2aa8e0" d="M6.6 10.8a15 15 0 0 0 6.6 6.6l2.2-2.2a1 1 0 0 1 1-.25 11.4 11.4 0 0 0 3.6.57 1 1 0 0 1 1 1V20a1 1 0 0 1-1 1A17 17 0 0 1 3 4a1 1 0 0 1 1-1h3.5a1 1 0 0 1 1 1c0 1.25.2 2.45.57 3.57a1 1 0 0 1-.25 1z"/></svg>
          0431 286 517
        </li>
        <li class="contact__item">
          <svg class="contact__icon" viewBox="0 0 24 24" aria-hidden="true"><rect x="2" y="5" width="20" height="14" rx="1.5" fill="#2aa8e0"/><path d="M3 6l9 7 9-7" fill="none" stroke="#fff" stroke-width="1.6"/></svg>
          rowan@tbk-plumbing.com.au
        </li>
      </ul>
    </div>
    <div class="abn-band">Company ABN - 73 215 904 386</div>
  </section>

  <section class="card card--back" aria-label="Card back">
    <div class="back-mark">
      <div class="back-mark__row">
        <span class="back-mark__name">tbk</span>
        <span class="back-mark__dot"></span>
      </div>
      <div class="back-mark__tag">plumbing services</div>
    </div>
  </section>
</main>
</body>
</html>
```